Construction company business card

One side to be the logo with the company name, The other side I would like: (Tomas verbick) Project manager 41 barrow crescent hallam 52917306224783(03) 9703 2428Info@gudeljgroup.comAnd then maybe a couple dot points saying what we do:Construction (commercial & industrial) Civil construction

Anything else please contact me!
Maybe curved st one edge of the card

Target Market(s)

Older clientele

Industry/Entity Type

Construction Company

Contact Information for Business Card

Read above

Colors
3277b5
1b1b1b
9d9d9d

Requirements
Must have
• Use my logo on one side
Nice to have
• Read above
Should not have
• Read above

```html
<!DOCTYPE html>
<html lang="en">
<head>
<meta charset="utf-8">
<title>Solidline Construction – Business Card</title>
<link rel="stylesheet" href="https://fonts.googleapis.com/css2?family=Work+Sans:wght@400;600&display=swap">
<style>
  :root {
    --brand-blue: #3277b5;
    --card-black: #1b1b1b;
    --card-grey: #9d9d9d;
    --page-bg: #0f0f0f;
    --text-white: #f2f2f2;
  }
  * { margin: 0; padding: 0; box-sizing: border-box; }
  html, body {
    width: 1200px;
    height: 900px;
    overflow: hidden;
    background: var(--page-bg);
    font-family: "Work Sans", Arial, sans-serif;
  }
  .sheet {
    width: 1200px;
    height: 900px;
    display: flex;
    flex-direction: column;
    align-items: center;
    justify-content: center;
    gap: 44px;
  }
  .card {
    position: relative;
    width: 620px;
    height: 354px;
    background: var(--card-black);
    border-bottom: 4px solid var(--brand-blue);
  }
  .brand {
    display: flex;
    align-items: center;
    gap: 14px;
    color: var(--brand-blue);
    font-weight: 600;
    text-transform: uppercase;
  }
  .brand-dot {
    border-radius: 50%;
    background: var(--brand-blue);
    flex: none;
  }
  .card-front {
    display: flex;
    align-items: center;
    justify-content: center;
  }
  .card-front .brand {
    flex-direction: column;
    font-size: 30px;
    letter-spacing: 2px;
    text-align: center;
    line-height: 1.15;
  }
  .card-front .brand-dot { width: 82px; height: 82px; }
  .card-back {
    display: flex;
    align-items: center;
  }
  .card-back .brand-area {
    width: 300px;
    display: flex;
    justify-content: center;
  }
  .card-back .brand {
    flex-direction: column;
    font-size: 26px;
    letter-spacing: 2px;
    text-align: center;
    line-height: 1.15;
  }
  .card-back .brand-dot { width: 96px; height: 96px; }
  .divider {
    width: 2px;
    height: 190px;
    background: var(--brand-blue);
  }
  .contact {
    padding-left: 40px;
    color: var(--text-white);
    font-size: 17px;
    line-height: 1.3;
  }
  .contact-name {
    color: var(--brand-blue);
    font-size: 22px;
    font-weight: 400;
    letter-spacing: 1px;
    text-transform: uppercase;
  }
  .contact-role { margin-bottom: 12px; letter-spacing: 0.5px; }
  .contact-address { margin-bottom: 10px; letter-spacing: 0.5px; }
  .contact-line {
    display: flex;
    align-items: center;
    gap: 8px;
    letter-spacing: 0.5px;
  }
  .contact-line svg { width: 12px; height: 12px; flex: none; }
</style>
</head>
<body>
<main class="sheet">
  <section class="card card-front">
    <div class="brand">
      <span class="brand-dot"></span>
      <span class="brand-name">Solidline<br>Construction</span>
    </div>
  </section>

  <section class="card card-back">
    <div class="brand-area">
      <div class="brand">
        <span class="brand-dot"></span>
        <span class="brand-name">Solidline<br>Construction</span>
      </div>
    </div>
    <div class="divider"></div>
    <div class="contact">
      <h1 class="contact-name">Tomas Verbick</h1>
      <p class="contact-role">Project manager</p>
      <p class="contact-address">41 barrow<br>crescent kelvale 5291</p>
      <p class="contact-line">
        <svg viewBox="0 0 12 12" aria-hidden="true"><path d="M3 1 L5 3.5 L4 5 Q5 7 7 8 L8.5 7 L11 9 L9.5 11 Q5 10.5 1 3 Z" fill="none" stroke="var(--brand-blue)" stroke-width="1.2"/></svg>
        73 0622 4783
      </p>
      <p class="contact-line">
        <svg viewBox="0 0 12 12" aria-hidden="true"><rect x="3" y="0.8" width="6" height="10.4" rx="1" fill="none" stroke="var(--brand-blue)" stroke-width="1.2"/><line x1="5" y1="9.2" x2="7" y2="9.2" stroke="var(--brand-blue)" stroke-width="1"/></svg>
        (03) 9418 6573
      </p>
      <p class="contact-line">
        <svg viewBox="0 0 12 12" aria-hidden="true"><rect x="0.8" y="2.5" width="10.4" height="7" fill="none" stroke="var(--brand-blue)" stroke-width="1.2"/><path d="M0.8 2.5 L6 6.5 L11.2 2.5" fill="none" stroke="var(--brand-blue)" stroke-width="1.2"/></svg>
        Info@verbickgroup.com
      </p>
    </div>
  </section>
</main>
</body>
</html>
```